ORLA - Óptica Médica - web design and concept

Website concept - Create and develop our website design and structure. ORLA is an optical store chain, and we are looking to establish our web and digital concept. In attachment there are several pictures about our stores and our logo.

The website structure should be user friendly. Colors should be light and the design as simple and minimalist as possible. There are different variations of the logothat can be used, check the file.

The website will include optical collections and sun collections as an online store. Also, a medical menu should be considered in order for clients to schedule optometry appointments. There should also be a menu for client assistance where the clients can read about glass maintenance in our workshop.
Updates

Low design quality

Number of Pages Required

5+ page

Font styles to use
Serif
Sans Serif

Requirements
Must have
• Must be user-friendly and minimalist.
• Please USE PICTURES FROM THE BRANDS we sell: MERUN, BOSKA, PNW, KOLE, BAMPE
Nice to have
• Nice to inspire: ZEK glasses (see website https://ch.shopzek.com/en/)
• Nice to inspire: https://merun-eyewear.com/
• Nice to ispire: https://www.pnwglobe.com/en/
Should not have
• Hysteric colors and shapes

```html
<!DOCTYPE html>
<html lang="en">
<head>
<meta charset="utf-8">
<title>ORLA Óptica Médica</title>
<link href="https://fonts.googleapis.com/css2?family=Lato:wght@300;400;700;900&display=swap" rel="stylesheet">
<style>
:root{
  --ink:#111111;
  --text:#333333;
  --muted:#666666;
  --line:#e2e2e2;
  --band:#f2f2f2;
  --white:#ffffff;
  --star:#e0a526;
  --star-off:#bbbbbb;
  --skin:#e2b89c;
  --skin-deep:#c98f6f;
  --hair:#6b4a34;
  --shirt:#c41f1f;
  --cap:#e0b034;
  --sage:#8e9c8c;
}
*{box-sizing:border-box;margin:0;padding:0}
html,body{width:1200px;height:2628px;overflow:hidden;background:var(--white)}
body{position:relative;font-family:"Lato",Arial,sans-serif;color:var(--text)}
.abs{position:absolute}

/* header */
.topbar{left:0;top:0;width:1200px;height:77px;border-bottom:1px solid var(--line)}
.topbar span{position:absolute;top:30px;font-size:13px;color:var(--text);display:flex;align-items:center;gap:8px}
.mainnav{left:0;top:77px;width:1200px;height:70px;border-bottom:1px solid var(--line);box-shadow:0 2px 4px rgba(0,0,0,.06)}
.mainnav a{position:absolute;top:24px;font-size:16px;color:var(--ink);text-decoration:none}
.logo-tab{left:532px;top:0;width:136px;height:186px;z-index:5}
.logo-tab svg{position:absolute;left:0;top:0}
.logo-tab .mark{position:absolute;left:50%;top:20px;transform:translateX(-50%);width:40px;height:40px;border:2px solid var(--ink)}
.logo-tab .name{position:absolute;left:0;right:0;top:76px;text-align:center;font-size:30px;letter-spacing:6px;color:var(--ink);font-weight:400}
.logo-tab .sub{position:absolute;left:0;right:0;top:116px;text-align:center;font-size:9px;letter-spacing:3px;color:var(--ink)}
.social{top:95px;display:flex;gap:10px;left:920px}
.social i{width:32px;height:32px;border:1.5px solid var(--ink);border-radius:50%;display:block;position:relative}
.social i.cart::after{content:"0";position:absolute;top:-12px;right:2px;font-size:10px;font-style:normal}

/* hero */
.hero-photo{left:640px;top:147px;width:560px;height:490px;
  clip-path:polygon(60px 0,100% 0,100% 462px,17px 487px,50px 280px);
  background:
    radial-gradient(ellipse 120px 150px at 52% 30%,var(--skin) 0,rgba(226,184,156,.9) 45%,rgba(226,184,156,0) 100%),
    radial-gradient(ellipse 200px 260px at 78% 25%,var(--hair) 0,rgba(107,74,52,.6) 50%,rgba(107,74,52,0) 100%),
    linear-gradient(180deg,rgba(255,255,255,0) 0,rgba(255,255,255,0) 58%,var(--shirt) 72%,#a5161a 100%),
    linear-gradient(90deg,#f4f1ee 0,#ece4dc 100%)}
.hero-title{left:145px;top:292px;font-size:42px;font-weight:700;color:var(--ink);letter-spacing:.5px}
.hero-copy{left:147px;top:352px;width:496px;font-size:14.5px;line-height:24px;color:var(--ink)}
.btn{position:absolute;height:45px;font-size:18px;font-weight:700;display:flex;align-items:center;justify-content:center}
.btn-outline{left:148px;top:420px;width:154px;border:2px solid var(--ink);color:var(--ink)}
.btn-solid{left:317px;top:420px;width:139px;background:var(--ink);color:var(--white)}

.brand{position:absolute;top:704px;font-size:24px;color:var(--ink);font-weight:900;letter-spacing:1px}

/* promo */
.tile{position:absolute}
.tile-label{position:absolute;border:2px solid var(--white);color:var(--white);font-size:24px;font-weight:300;letter-spacing:.5px;padding:4px 18px;white-space:nowrap}
.tile-graduated{left:75px;top:832px;width:512px;height:328px;background:
  radial-gradient(ellipse 150px 60px at 72% 4%,var(--cap) 0,rgba(224,176,52,.8) 50%,rgba(224,176,52,0) 100%),
  radial-gradient(ellipse 130px 150px at 68% 42%,var(--skin) 0,rgba(226,184,156,.85) 50%,rgba(226,184,156,0) 100%),
  radial-gradient(ellipse 60px 50px at 40% 96%,var(--cap) 0,rgba(224,176,52,0) 100%),
  linear-gradient(90deg,#d6d6d6 0,#c9c9c9 45%,#a89d94 62%,#3a3330 88%,#262220 100%)}
.tile-sun{left:883px;top:832px;width:244px;height:251px;background:
  radial-gradient(ellipse 70px 90px at 55% 28%,var(--skin-deep) 0,rgba(201,143,111,.7) 50%,rgba(201,143,111,0) 100%),
  radial-gradient(ellipse 110px 120px at 70% 90%,#1a1a1a 0,rgba(26,26,26,0) 100%),
  linear-gradient(135deg,#2a2a2a,#5d4f47 55%,#2e2e2e)}
.tile-kids{left:615px;top:1111px;width:512px;height:250px;background:
  linear-gradient(180deg,rgba(0,0,0,0) 0,rgba(0,0,0,0) 80%,rgba(205,212,200,.95) 82%,#c7cec1 100%),
  radial-gradient(ellipse 110px 100px at 53% 70%,var(--skin) 0,rgba(226,184,156,.8) 50%,rgba(226,184,156,0) 100%),
  radial-gradient(ellipse 170px 70px at 53% 38%,#8a5a3a 0,rgba(138,90,58,0) 100%),
  linear-gradient(180deg,#9aa696,#8b998b)}
.offer{left:615px;top:832px;width:245px;height:251px;background:linear-gradient(90deg,#f3f3f3 50%,#e6e6e6 50%);text-align:center;border:1px solid var(--line)}
.offer h3{font-size:66px;font-weight:900;color:#2a2a2a;margin-top:38px;line-height:1}
.offer p{font-size:13px;line-height:22px;color:var(--ink);margin:18px 18px 0}
.offer b{display:inline-block;margin-top:14px;background:var(--ink);color:var(--white);font-size:13px;padding:12px 22px;font-weight:700}
.frame-box{border:1px solid var(--line)}
.shot-black{background:radial-gradient(ellipse 42% 22% at 50% 50%,rgba(25,25,25,.55) 0,rgba(25,25,25,.2) 55%,rgba(25,25,25,0) 100%),linear-gradient(#fff,#f3f3f3)}
.shot-dark{background:radial-gradient(ellipse 42% 24% at 50% 48%,rgba(15,15,15,.75) 0,rgba(15,15,15,.3) 55%,rgba(15,15,15,0) 100%),linear-gradient(#fff,#f1f1f1)}
.shot-silver{background:radial-gradient(ellipse 42% 24% at 50% 50%,rgba(70,78,95,.6) 0,rgba(120,128,140,.25) 55%,rgba(120,128,140,0) 100%),linear-gradient(#fff,#f4f4f4)}
.shot-orange{background:radial-gradient(ellipse 44% 26% at 50% 50%,rgba(240,160,30,.75) 0,rgba(240,170,40,.3) 55%,rgba(240,170,40,0) 100%),radial-gradient(ellipse 30% 14% at 50% 52%,rgba(40,30,20,.5) 0,rgba(40,30,20,0) 100%),#fff}

/* products */
.section-title{left:0;width:1200px;text-align:center;font-weight:900;color:var(--ink)}
.card{position:absolute;top:1515px;width:255px;height:319px;border:1px solid var(--line);background:var(--white)}
.card .ribbon{position:absolute;right:8px;top:0;width:18px;height:92px;background:var(--ink);color:var(--white);font-size:10px;writing-mode:vertical-rl;text-align:center;padding-top:10px}
.card .shot{position:absolute;left:15px;top:70px;width:223px;height:150px}
.tool{position:absolute;top:16px;height:33px;display:flex;align-items:center;justify-content:center}
.meta{position:absolute;top:1850px;width:255px;text-align:center}
.stars{font-size:12px;letter-spacing:1px;color:var(--star)}
.stars em{color:var(--star-off);font-style:normal}
.meta h4{font-size:16px;font-weight:700;letter-spacing:2px;color:var(--ink);margin-top:4px}
.meta p{font-size:18px;font-weight:700;color:var(--ink);margin-top:8px;letter-spacing:1px}
.pager{top:1952px;width:28px;height:28px;border:1px solid #bbb;display:flex;align-items:center;justify-content:center}

/* guarantees */
.guarantees{left:0;top:2050px;width:1200px;height:310px;background:var(--band);border-top:3px solid #e9e9e9}
.gbox{position:absolute;top:2150px;width:194px;height:175px;background:var(--white);text-align:center}
.gbox svg{margin-top:32px}
.gbox p{font-size:17px;font-weight:700;color:var(--ink);line-height:22px;margin-top:16px;padding:0 10px}

/* footer */
.foot-logo{left:68px;top:2404px;width:124px;height:180px}
.foot-logo svg{position:absolute;left:0;top:0}
.foot-logo .mark{position:absolute;left:44px;top:22px;width:36px;height:36px;border:2px solid var(--ink)}
.foot-logo .name{position:absolute;left:0;right:0;top:76px;text-align:center;font-size:28px;letter-spacing:5px;color:var(--ink)}
.foot-logo .sub{position:absolute;left:0;right:0;top:112px;text-align:center;font-size:8px;letter-spacing:2px;color:var(--ink)}
.fh{position:absolute;top:2402px;font-size:17px;color:var(--text);line-height:22px}
.ft{position:absolute;font-size:13px;line-height:24px;color:var(--text)}
.cards{left:848px;top:2498px;display:flex;gap:7px}
.cards i{display:block;width:37px;height:22px;border:1px solid #ccc;background:#e9eef5;border-radius:2px}
.copybar{left:0;top:2567px;width:1200px;height:61px;background:var(--band)}
.copybar span{position:absolute;left:75px;top:22px;font-size:13px;color:var(--text)}
.copybar .social2{position:absolute;left:1006px;top:14px;display:flex;gap:9px}
.copybar .social2 i{width:32px;height:32px;border:1px solid #888;border-radius:50%;display:block}
</style>
</head>
<body>

<!-- header -->
<div class="abs topbar">
  <span style="left:75px">
    <svg width="12" height="12" viewBox="0 0 24 24"><path d="M6.6 10.8a15 15 0 006.6 6.6l2.2-2.2c.3-.3.7-.4 1-.2 1.1.4 2.3.6 3.6.6.6 0 1 .4 1 1V20c0 .6-.4 1-1 1A17 17 0 013 4c0-.6.4-1 1-1h3.5c.6 0 1 .4 1 1 0 1.3.2 2.5.6 3.6.1.3 0 .7-.2 1z" fill="#222"/></svg>
    Phone: 1300 552 904
  </span>
  <span style="left:912px">
    <svg width="13" height="10" viewBox="0 0 26 20"><rect width="26" height="20" rx="2" fill="#222"/><path d="M1 2l12 9 12-9" stroke="#fff" stroke-width="2" fill="none"/></svg>
    email: info@orlaopticamedica.com
  </span>
</div>
<nav class="abs mainnav">
  <a style="left:75px">Home</a>
  <a style="left:154px">About us</a>
  <a style="left:254px">Products</a>
  <a style="left:355px">Contact Us</a>
  <a style="left:763px">Blog</a>
  <a style="left:838px">Store</a>
</nav>
<div class="abs logo-tab">
  <svg width="136" height="186" viewBox="0 0 136 186"><path d="M1 0V156L68 184L135 156V0" fill="#fff" stroke="#dddddd" stroke-width="1.5"/></svg>
  <div class="mark"></div>
  <div class="name">ORLA</div>
  <div class="sub">ÓPTICA MEDICA</div>
</div>
<div class="abs social">
  <i class="cart"><svg width="30" height="30" viewBox="0 0 30 30"><path d="M8 10h2l2 8h8l2-6H11" stroke="#111" stroke-width="1.8" fill="none"/><circle cx="13" cy="21" r="1.3" fill="#111"/><circle cx="19" cy="21" r="1.3" fill="#111"/></svg></i>
  <i aria-label="Social link"></i><i aria-label="Social link"></i><i aria-label="Social link"></i><i aria-label="Social link"></i>
</div>

<!-- hero -->
<svg class="abs" style="left:0;top:147px" width="1200" height="660" viewBox="0 0 1200 660">
  <polygon points="0,515 1200,462 1200,660 0,660" fill="#f2f2f2"/>
  <path d="M92 190l-14 14 14 14" stroke="#222" stroke-width="5" fill="none"/>
  <path d="M1106 190l14 14-14 14" stroke="#222" stroke-width="5" fill="none"/>
</svg>
<div class="abs hero-photo" role="img" aria-label="Photo of a smiling woman in a red shirt adjusting black eyeglasses"></div>
<h1 class="abs hero-title">ORLA OPTICA MEDICA</h1>
<p class="abs hero-copy">BOOK YOUR APPOINTMENT WITH US. We will be happy to help you and offer you the best solution for your visual health problems.</p>
<div class="btn btn-outline">SHOP NOW</div>
<div class="btn btn-solid">CALL US!</div>

<div class="brand" style="left:148px">WARDEN</div>
<div class="brand" style="left:340px">CORSO</div>
<div class="brand" style="left:530px;font-weight:700">JULES MARO</div>
<div class="brand" style="left:740px">FENVI</div>
<div class="brand" style="left:905px;font-weight:700">ADELA SORIN</div>
<div class="abs" style="left:0;top:800px;width:1200px;height:3px;background:#e9e9e9"></div>

<!-- promo grid -->
<div class="tile tile-graduated" role="img" aria-label="Photo of a woman in a yellow cap wearing black glasses, with the store name on a brick wall">
  <div class="tile-label" style="left:190px;top:250px">GRADUATED FRAME</div>
</div>
<div class="tile offer">
  <h3>50%</h3>
  <p>Enim aliquam nihil. Id mauris turpis. Condimentum</p>
  <b>GET STARTED</b>
</div>
<div class="tile tile-sun" role="img" aria-label="Photo of a woman wearing dark sunglasses">
  <div class="tile-label" style="left:33px;top:95px">SUNGLASS</div>
</div>
<div class="tile frame-box shot-black" role="img" aria-label="Product photo of black eyeglass frames" style="left:75px;top:1190px;width:245px;height:171px"></div>
<div class="tile frame-box shot-dark" role="img" aria-label="Product photo of dark aviator sunglasses" style="left:342px;top:1190px;width:245px;height:171px"></div>
<div class="tile tile-kids" role="img" aria-label="Photo of a child in glasses peeking over a table">
  <div class="tile-label" style="left:122px;top:104px">SPECIAL CHILDREN</div>
</div>

<!-- products -->
<h2 class="abs section-title" style="top:1420px;font-size:40px">OUR PRODUCTS</h2>
<p class="abs section-title" style="top:1477px;font-size:11px;font-weight:700;letter-spacing:.5px;color:var(--text)">A passage of Lorem Ipsum you need here</p>

<div class="card" style="left:60px">
  <div class="shot shot-black" role="img" aria-label="Product photo of black eyeglass frames"></div>
  <div class="tool" style="left:18px;width:35px;background:var(--ink)">
    <svg width="14" height="13" viewBox="0 0 24 22"><path d="M12 21S2 14 2 7.5A5 5 0 0112 5a5 5 0 0110 2.5C22 14 12 21 12 21z" stroke="#fff" stroke-width="2.4" fill="none"/></svg>
  </div>
  <div class="tool" style="left:60px;width:38px;border:1px solid #999">
    <svg width="16" height="10" viewBox="0 0 24 14"><path d="M1 7C5 1 19 1 23 7C19 13 5 13 1 7z" fill="#222"/><circle cx="12" cy="7" r="3" fill="#fff"/></svg>
  </div>
  <div class="tool" style="left:176px;width:38px;border:1px solid #999">
    <svg width="12" height="10" viewBox="0 0 12 10"><path d="M2 1h9M2 5h9M2 9h9" stroke="#222" stroke-width="1.4"/></svg>
  </div>
  <div class="abs" style="left:0;bottom:0;width:253px;height:31px;background:var(--ink);color:#fff;font-size:12px;font-weight:700;letter-spacing:2px;text-align:center;line-height:31px">ADD TO CART</div>
</div>
<div class="card" style="left:337px">
  <div class="shot shot-black" role="img" aria-label="Product photo of black eyeglass frames"></div>
  <div class="ribbon">New Arrival</div>
</div>
<div class="card" style="left:612px">
  <div class="shot shot-silver" role="img" aria-label="Product photo of silver aviator sunglasses"></div>
</div>
<div class="card" style="left:887px">
  <div class="shot shot-orange" role="img" aria-label="Product photo of orange framed sunglasses"></div>
  <div class="ribbon">New Arrival</div>
</div>

<div class="meta" style="left:60px"><div class="stars">★★★<em>★★</em></div><h4>GRADUATED FRAME</h4><p>$235.00</p></div>
<div class="meta" style="left:337px"><div class="stars">★★★<em>★★</em></div><h4>SPECIAL CHILDREN</h4><p>$235.00</p></div>
<div class="meta" style="left:612px"><div class="stars">★★★<em>★★</em></div><h4>SUN GLASSES</h4><p>$235.00</p></div>
<div class="meta" style="left:887px"><div class="stars">★★★<em>★★</em></div><h4>SUN GLASSES</h4><p>$235.00</p></div>

<div class="abs pager" style="left:566px"><svg width="8" height="10"><path d="M6 1L2 5l4 4" stroke="#222" stroke-width="1.5" fill="none"/></svg></div>
<div class="abs pager" style="left:603px"><svg width="8" height="10"><path d="M2 1l4 4-4 4" stroke="#222" stroke-width="1.5" fill="none"/></svg></div>

<!-- guarantees -->
<div class="abs guarantees"></div>
<h2 class="abs section-title" style="top:2082px;font-size:28px;font-weight:700">OUR GUARANTEES</h2>
<div class="gbox" style="left:75px">
  <svg width="90" height="52" viewBox="0 0 90 52"><circle cx="28" cy="16" r="12" fill="#111"/><circle cx="62" cy="16" r="12" fill="#111"/><path d="M10 52c0-14 8-22 18-22s18 8 18 22zM44 52c0-14 8-22 18-22s18 8 18 22z" fill="#111"/></svg>
  <p>ORLA CHILDHOOD GUARANTEE</p>
</div>
<div class="gbox" style="left:290px">
  <svg width="60" height="52" viewBox="0 0 60 52"><path d="M4 12h34v30H4zM38 22h10l8 10v10H38z" fill="#111"/><circle cx="14" cy="44" r="6" fill="#111" stroke="#fff" stroke-width="2"/><circle cx="46" cy="44" r="6" fill="#111" stroke="#fff" stroke-width="2"/><path d="M21 18v18M12 27h18" stroke="#fff" stroke-width="4"/></svg>
  <p>ORLA ACCIDENT WARRANTY</p>
</div>
<div class="gbox" style="left:504px">
  <svg width="40" height="52" viewBox="0 0 40 52"><path d="M10 22v-8a10 10 0 0120 0v8" stroke="#111" stroke-width="5" fill="none"/><rect x="2" y="22" width="36" height="28" rx="3" fill="#111"/></svg>
  <p>ORLA SECURITY</p>
</div>
<div class="gbox" style="left:719px">
  <svg width="56" height="52" viewBox="0 0 56 52"><path d="M2 26C10 12 20 8 28 8s18 4 26 18C46 40 36 44 28 44S10 40 2 26z" fill="#111"/><circle cx="28" cy="26" r="10" fill="#fff"/><circle cx="28" cy="26" r="6" fill="#111"/></svg>
  <p>ORLA VISION</p>
</div>
<div class="gbox" style="left:933px">
  <svg width="46" height="52" viewBox="0 0 46 52"><rect x="3" y="8" width="40" height="42" rx="3" fill="#111"/><rect x="10" y="2" width="5" height="10" fill="#111"/><rect x="31" y="2" width="5" height="10" fill="#111"/><path d="M14 31l7 7 12-13" stroke="#fff" stroke-width="4" fill="none"/></svg>
  <p>MANUFACTURER'S WARRANTY</p>
</div>

<!-- footer -->
<div class="abs foot-logo">
  <svg width="124" height="180" viewBox="0 0 124 180"><path d="M1 1H123V152L62 179L1 152Z" fill="#fff" stroke="#d6d6d6" stroke-width="1.5"/></svg>
  <div class="mark"></div>
  <div class="name">ORLA</div>
  <div class="sub">ÓPTICA MEDICA</div>
</div>
<div class="fh" style="left:213px">WELCOME TO<br>ORLA OPTICA MEDICA</div>
<p class="ft" style="left:217px;top:2455px;width:240px">ORLA OPTICA opens its doors with a clear purpose: to take care of you. Our priority is your visual health,....</p>
<div class="fh" style="left:492px">LOCATION</div>
<p class="ft" style="left:496px;top:2442px">
  <svg width="10" height="13" viewBox="0 0 10 14" style="margin-left:-2px"><path d="M5 0a5 5 0 015 5c0 4-5 9-5 9S0 9 0 5a5 5 0 015-5z" fill="#333"/><circle cx="5" cy="5" r="2" fill="#fff"/></svg>
  &nbsp;#123 Lorium ipsum,<br>&nbsp;&nbsp;&nbsp;&nbsp;dolor amit,<br>&nbsp;&nbsp;&nbsp;&nbsp;City name.
</p>
<div class="fh" style="left:682px">CALL US</div>
<p class="ft" style="left:684px;top:2442px">
  <svg width="12" height="12" viewBox="0 0 24 24"><path d="M6.6 10.8a15 15 0 006.6 6.6l2.2-2.2c.3-.3.7-.4 1-.2 1.1.4 2.3.6 3.6.6.6 0 1 .4 1 1V20c0 .6-.4 1-1 1A17 17 0 013 4c0-.6.4-1 1-1h3.5c.6 0 1 .4 1 1 0 1.3.2 2.5.6 3.6.1.3 0 .7-.2 1z" fill="#333"/></svg>
  &nbsp;1300 552 904
</p>
<div class="fh" style="left:850px">EMAIL</div>
<p class="ft" style="left:851px;top:2442px">
  <svg width="13" height="10" viewBox="0 0 26 20"><rect width="26" height="20" rx="2" fill="#333"/><path d="M1 2l12 9 12-9" stroke="#fff" stroke-width="2" fill="none"/></svg>
  &nbsp;info@orlaopticamedica.com
</p>
<div class="abs cards" aria-label="Accepted payment methods"><i></i><i></i><i></i><i></i><i></i><i></i></div>
<svg class="abs" style="left:1157px;top:2517px" width="10" height="8"><path d="M1 7l4-5 4 5" stroke="#333" stroke-width="1.8" fill="none"/></svg>

<div class="abs copybar">
  <span>© Copyright 2018 www.orlaoptica.net . All Rights Reserved &nbsp;|&nbsp; Privacy Policy.</span>
  <div class="social2"><i aria-label="Social link"></i><i aria-label="Social link"></i><i aria-label="Social link"></i></div>
</div>

</body>
</html>
```